Irrigation Business needs their business cards modernised and revamped

I would like to keep my current logo, colours and revamp the format of the card.

I would like the card to be clean yet important.

Im not sure if you include texture but i would like the named logo to be indented into the card etc.

show me something alive and free something thats clinical to the point yet has a feel of achievement. i would like people to go nice card.

Target Market(s)

high end clients, corporate, sports field manger, the guys that make the decisions

Industry/Entity Type

Business

Contact Information for Business Card

nformation to be included

Dean Harlow (Director)
0487305526
dean@kolvat.biz
www.kestonfieldworks.com

instagram logo
google logo
facebook logo

Colors

Designer to choose colors to be used in the design.

Requirements
Nice to have
• indentations a really nice feel to the card good texture

```html
<!DOCTYPE html>
<html lang="en">
<head>
<meta charset="utf-8">
<title>Keston Fieldworks – Business Card</title>
<link href="https://fonts.googleapis.com/css2?family=Roboto:wght@400;700;900&display=swap" rel="stylesheet">
<style>
  :root {
    --backdrop: #2b2c2e;
    --card-white: #f7f7f5;
    --card-green: #4cb274;
    --brand-blue: #2f73b8;
    --sky-blue: #3aa6d9;
    --brand-green: #3fa95a;
    --ink-white: #ffffff;
  }
  * { margin: 0; padding: 0; box-sizing: border-box; }
  html, body {
    width: 1200px; height: 840px; overflow: hidden;
    background: var(--backdrop);
    font-family: "Roboto", Arial, sans-serif;
  }
  .canvas { position: relative; width: 1200px; height: 840px; }

  .card {
    position: absolute; width: 700px; height: 380px;
    border-radius: 4px; overflow: hidden;
    box-shadow: 0 14px 30px rgba(0,0,0,.45);
  }

  /* Front */
  .card-front {
    left: 150px; top: 35px;
    background: var(--card-white);
    display: flex; flex-direction: column; align-items: center; justify-content: center;
  }
  .front-mark {
    width: 78px; height: 78px; border-radius: 50%;
    background: var(--sky-blue);
    margin-bottom: 18px;
  }
  .front-name {
    font-weight: 900; font-size: 40px; letter-spacing: 1px;
    color: var(--brand-blue); text-transform: uppercase;
  }
  .social-row { display: flex; gap: 8px; margin-top: 20px; }
  .social-dot {
    width: 22px; height: 22px; border-radius: 50%;
    background: var(--brand-blue);
  }

  /* Back */
  .card-back {
    left: 350px; top: 430px;
    background: var(--card-green);
  }
  .back-brand {
    position: absolute; left: 44px; top: 52px;
    display: flex; flex-direction: column; align-items: flex-start;
  }
  .back-mark {
    width: 52px; height: 52px; border-radius: 50%;
    background: var(--ink-white); margin-left: 40px; margin-bottom: 10px;
  }
  .back-name {
    font-weight: 900; font-size: 24px; letter-spacing: .5px;
    color: var(--ink-white); text-transform: uppercase;
  }
  .contact-block { position: absolute; left: 44px; top: 210px; }
  .person-name {
    font-weight: 700; font-size: 17px; color: var(--brand-blue);
    text-transform: uppercase;
  }
  .person-role {
    font-size: 16px; color: var(--ink-white); text-transform: uppercase;
    margin-bottom: 14px;
  }
  .contact-line {
    display: flex; align-items: center; gap: 10px;
    font-size: 15px; color: var(--ink-white); line-height: 24px;
  }
  .contact-icon { width: 14px; height: 14px; flex: none; }

  .back-emblem {
    position: absolute; right: -30px; top: -40px;
    width: 380px; height: 380px;
  }
</style>
</head>
<body>
<div class="canvas">

  <section class="card card-front">
    <div class="front-mark"></div>
    <div class="front-name">Keston Fieldworks</div>
    <div class="social-row">
      <span class="social-dot"></span>
      <span class="social-dot"></span>
      <span class="social-dot"></span>
    </div>
  </section>

  <section class="card card-back">
    <div class="back-brand">
      <div class="back-mark"></div>
      <div class="back-name">Keston Fieldworks</div>
    </div>

    <div class="contact-block">
      <div class="person-name">Dean Harlow</div>
      <div class="person-role">Director</div>
      <div class="contact-line">
        <svg class="contact-icon" viewBox="0 0 14 14"><circle cx="7" cy="7" r="7" fill="#2f73b8"/><path d="M4 4.5c0 3 2.5 5.5 5.5 5.5l.8-1.3-1.6-.9-.7.7C6.8 8 6 7.2 5.5 6l.7-.7-.9-1.6z" fill="#fff"/></svg>
        <span>0487305526</span>
      </div>
      <div class="contact-line">
        <svg class="contact-icon" viewBox="0 0 14 14"><circle cx="7" cy="7" r="7" fill="#2f73b8"/><rect x="3.5" y="4.5" width="7" height="5" fill="none" stroke="#fff" stroke-width="1"/><path d="M3.5 4.5 7 7.5l3.5-3" fill="none" stroke="#fff" stroke-width="1"/></svg>
        <span>dean@kolvat.biz</span>
      </div>
      <div class="contact-line">
        <svg class="contact-icon" viewBox="0 0 14 14"><circle cx="7" cy="7" r="7" fill="#2f73b8"/><circle cx="7" cy="7" r="3.5" fill="none" stroke="#fff" stroke-width="1"/><path d="M3.5 7h7M7 3.5v7" stroke="#fff" stroke-width="1"/></svg>
        <span>kestonfieldworks.com</span>
      </div>
    </div>

    <svg class="back-emblem" viewBox="0 0 380 380">
      <circle cx="190" cy="190" r="186" fill="none" stroke="#ffffff" stroke-width="3"/>
      <circle cx="190" cy="190" r="176" fill="#2f73b8"/>
      <circle cx="190" cy="190" r="160" fill="#3aa6d9"/>
    </svg>
  </section>

</div>
</body>
</html>
```